Chimney Service company needs new business card design

We need a updated business card with our new logo added. We provide a full range of chimney services throughout Vermont and New Hampshire. The business card will be one sided and color. Attached is our current business card another document showing all the information we would like on the card.
We dont like a lot of flashy colors.... here is a link to our website to get an idea of our branding www.flueguardianvt.example

Target Market(s)

homeowners

Industry/Entity Type

Business

Contact Information for Business Card

See attached sheet for content.

Font styles to use
Serif
Sans Serif

Requirements
Must have
• all information provided on separate sheet
Should not have
• Additional information that may clogg up design

```html
<!DOCTYPE html>
<html lang="en">
<head>
<meta charset="utf-8">
<title>Flue Guardian – Business Card</title>
<link href="https://fonts.googleapis.com/css2?family=Cinzel:wght@400;500&family=Lato:wght@400;700&display=swap" rel="stylesheet">
<style>
  :root{
    --stage:#2a2a2a;
    --card-white:#ffffff;
    --card-black:#161616;
    --ink:#2b2b2b;
    --ink-soft:#444444;
    --accent:#a8191c;
    --paper-text:#f2f2f2;
  }
  *{margin:0;padding:0;box-sizing:border-box}
  html,body{width:1200px;height:738px;overflow:hidden;background:var(--stage)}
  .stage{position:relative;width:1200px;height:738px;display:flex;align-items:center;justify-content:center;gap:40px}
  .card{position:relative;width:540px;height:309px;border-radius:3px;box-shadow:0 10px 30px rgba(0,0,0,.45)}

  /* back */
  .card--back{background:var(--card-black);color:var(--paper-text)}
  .back__brand{position:absolute;left:0;right:0;top:108px;display:flex;align-items:center;justify-content:center;gap:16px}
  .brand-square{width:38px;height:38px;border:4px solid currentColor}
  .brand-name{font-family:"Cinzel",serif;font-weight:400;font-size:30px;letter-spacing:1px}
  .back__tagline{position:absolute;left:0;right:0;bottom:28px;text-align:center;font-family:"Cinzel",serif;font-size:12.5px;letter-spacing:.8px}

  /* front */
  .card--front{background:var(--card-white);color:var(--ink)}
  .front__brand{position:absolute;left:28px;top:78px;width:240px;display:flex;flex-direction:column;align-items:center;gap:18px;color:var(--ink)}
  .front__brand .brand-square{width:86px;height:86px;border-width:7px}
  .front__brand .brand-name{font-size:26px}
  .front__rule{position:absolute;left:292px;top:64px;width:2px;height:152px;background:var(--accent)}
  .front__info{position:absolute;left:312px;top:60px;font-family:"Lato",sans-serif}
  .contact{list-style:none;font-size:12.5px;line-height:16px;color:var(--ink)}
  .contact li{display:flex;align-items:center;gap:10px}
  .contact svg{width:10px;height:10px;fill:var(--accent);flex:none}
  .services__title{margin-top:10px;font-family:"Cinzel",serif;font-weight:500;font-size:15px;color:var(--accent);letter-spacing:.3px}
  .services{list-style:none;font-size:12.5px;line-height:16px;color:var(--ink-soft);margin-top:2px}
  .front__footer{position:absolute;left:0;right:0;bottom:30px;text-align:center;font-family:"Cinzel",serif;font-size:13px;color:var(--ink);letter-spacing:.5px}
  .front__footer .since{font-family:"Lato",sans-serif;color:var(--accent);letter-spacing:0}
</style>
</head>
<body>
<main class="stage">
  <section class="card card--back" aria-label="Card back">
    <div class="back__brand">
      <span class="brand-square"></span>
      <span class="brand-name">FLUE GUARDIAN</span>
    </div>
    <p class="back__tagline">Fully Insured–Free Estimates | Family Owned and Operated</p>
  </section>

  <section class="card card--front" aria-label="Card front">
    <div class="front__brand">
      <span class="brand-square"></span>
      <span class="brand-name">FLUE GUARDIAN</span>
    </div>
    <div class="front__rule"></div>
    <div class="front__info">
      <ul class="contact">
        <li><svg viewBox="0 0 10 10"><path d="M2 0h2l1 2.5-1.3 1a6 6 0 0 0 2.8 2.8l1-1.3L10 6v2c0 1-1 2-2 2A8 8 0 0 1 0 2c0-1 1-2 2-2z"/></svg>802-555-0147</li>
        <li><svg viewBox="0 0 10 10"><path d="M0 2h10v6H0zM0 2l5 3.5L10 2" /></svg>info@flueguardianvt.example</li>
        <li><svg viewBox="0 0 10 10"><circle cx="5" cy="5" r="4.5"/></svg>www.flueguardianvt.example</li>
      </ul>
      <h2 class="services__title">SERVICES WE PROVIDE</h2>
      <ul class="services">
        <li>Full Masonry Services</li>
        <li>Historic chimney restoration</li>
        <li>Stainless steel liners</li>
        <li>New Chimney installations</li>
        <li>FSCA Certified Chimney sweeps</li>
      </ul>
    </div>
    <p class="front__footer">SERVING VT AND NEW HAMPSHIRE-<span class="since">since 1989</span></p>
  </section>
</main>
</body>
</html>
```